Business Cards - New Logo Rebranding

Hello We know have a red and blue logo and are looking to create new cards. We are looking for the best creativity of the new logo merged with some of the existing artwork provided.

Target Market(s)

Realtors

Industry/Entity Type

Real Estate

Contact Information for Business Card

New logo with rebranded colors

Requirements
Must have
• Creative use of the new logo

```html
<!DOCTYPE html>
<html lang="en">
<head>
<meta charset="utf-8">
<title>Keystone Inspection Group – Business Cards</title>
<link rel="stylesheet" href="https://fonts.googleapis.com/css2?family=Arimo:wght@400;700&display=swap">
<style>
  :root {
    --stage: #1c1c1e;
    --brand-blue: #0b72c2;
    --brand-red: #e0283a;
    --paper: #ffffff;
    --ink-white: #ffffff;
  }
  * { box-sizing: border-box; margin: 0; padding: 0; }
  html, body {
    width: 1200px; height: 874px; overflow: hidden;
    background: var(--stage);
    font-family: "Arimo", Arial, sans-serif;
  }
  .canvas {
    position: relative; width: 1200px; height: 874px;
  }
  .card {
    position: absolute; left: 290px;
    width: 620px; height: 354px;
    border-radius: 22px; overflow: hidden;
    box-shadow: 0 18px 40px rgba(0,0,0,0.55);
  }
  /* Front */
  .card-front { top: 50px; background: var(--brand-blue); color: var(--ink-white); }
  .front-mark {
    position: absolute; left: 0; right: 0; top: 78px;
    display: flex; flex-direction: column; align-items: center; gap: 18px;
  }
  .mark-circle {
    width: 118px; height: 118px; border-radius: 50%;
    border: 5px solid var(--ink-white);
  }
  .brand-name {
    font-weight: 700; font-size: 30px; letter-spacing: 1px; text-transform: uppercase;
  }
  .services {
    position: absolute; left: 0; right: 0; top: 280px;
    text-align: center; font-size: 17px; letter-spacing: 0.5px; text-transform: uppercase;
  }
  /* Back */
  .card-back { top: 454px; background: var(--paper); }
  .back-mark {
    position: absolute; left: 0; right: 0; top: 34px;
    display: flex; flex-direction: column; align-items: center; gap: 12px;
  }
  .back-mark .mark-circle { width: 104px; height: 104px; border-color: var(--brand-red); }
  .back-mark .brand-name { font-size: 26px; color: var(--brand-blue); }
  .accent-line {
    position: absolute; left: 0; right: 0; top: 206px; height: 4px;
    background: var(--brand-red);
  }
  .contact-band {
    position: absolute; left: 0; right: 0; top: 216px; bottom: 0;
    background: var(--brand-blue); color: var(--ink-white);
    display: flex; align-items: center; justify-content: center; gap: 22px;
  }
  .person { text-align: right; }
  .person-name { font-weight: 700; font-size: 24px; }
  .person-title { font-size: 15px; margin-top: 4px; }
  .person-email { font-size: 15px; margin-top: 4px; }
  .divider { width: 2px; height: 82px; background: var(--ink-white); }
  .contact-list { list-style: none; font-size: 16px; }
  .contact-list li { display: flex; align-items: center; gap: 10px; line-height: 26px; }
  .contact-list svg { width: 15px; height: 15px; fill: none; stroke: var(--ink-white); stroke-width: 2; }
</style>
</head>
<body>
<main class="canvas">
  <section class="card card-front" aria-label="Card front">
    <div class="front-mark">
      <div class="mark-circle"></div>
      <div class="brand-name">Keystone Inspection Group</div>
    </div>
    <p class="services">Home • Sewer • Mold • Commercial • Termite • Roof</p>
  </section>

  <section class="card card-back" aria-label="Card back">
    <div class="back-mark">
      <div class="mark-circle"></div>
      <div class="brand-name">Keystone Inspection Group</div>
    </div>
    <div class="accent-line"></div>
    <div class="contact-band">
      <div class="person">
        <div class="person-name">Dana Whitfield</div>
        <div class="person-title">Certified Mold Inspector</div>
        <div class="person-email">dana@keystoneinspect.com</div>
      </div>
      <div class="divider"></div>
      <ul class="contact-list">
        <li><svg viewBox="0 0 16 16"><path d="M3 2h3l1 3-2 1.5a8 8 0 0 0 4.5 4.5L11 9l3 1v3a1 1 0 0 1-1 1A11 11 0 0 1 2 3a1 1 0 0 1 1-1z"/></svg>800.555.0142</li>
        <li><svg viewBox="0 0 16 16"><rect x="4" y="1" width="8" height="14" rx="1.5"/><line x1="7" y1="12.5" x2="9" y2="12.5"/></svg>562.555.0187</li>
        <li><svg viewBox="0 0 16 16"><circle cx="8" cy="8" r="6.5"/><ellipse cx="8" cy="8" rx="2.8" ry="6.5"/><line x1="1.5" y1="8" x2="14.5" y2="8"/></svg>www.KeystoneInspect.com</li>
      </ul>
    </div>
  </section>
</main>
</body>
</html>
```